Eyecatching website design for commercial lighting business

This contest is all about the graphic design aspect. We need a striking website design for a commercial lighting company. We want something really eye catching to introduce people to our range of induction and LED lights which save businesses money on maintenance and electricity costs.

To be successful in this contest you will need to provide a design and pictures for the pages listed below.

We are using the platform velbrin.com.au and you can see the attached template which everything will be loaded into so we just need HTML files which we can upload and we can do everything else from Velbrin.

The final design should be strong and clean and use the colours and textures in the attached business card file.

Detailed requirements:

Please see attached screenshot of the website template, all we need is a fantastic graphic design and improvement/ incorporation of our logo for the following pages
Page Headings:
1. Home
About Us, Contact Us, snapshot of and link to Blog

Each of the below pages will have several paragraphs of text followed by a list of suitable products which is generated from our product catalogue.

2. Car Park Lighting
3. Educational Lighting
4. Hospitality Lighting
5. Office & Shop Lighting
6. Warehouse Lighting

Some of the website we have seen which are similar in nature are:
http://www.quorvanlamps.com.au/
http://www.tibrox.com/
http://www.gandowlumen.net/commercial-led
but we really want a modern, eye catching and memorable design

Some of the designs built on Velbrin that we like are:

http://www.pemberhollow.com.au/
http://www.marwickgoods.com.au/
http://www.kelmorabay.com.au/

I've also uploaded a couple of photos that we love. We'd like something similar for each industry.

Target Market(s)

Company Owners, Maintenance & Facilities Managers, Electrical Contractors

Industry/Entity Type

Electrical

Coding

Coded - Design and coding required

Number of Pages Required

5+ page

Font styles to use
Sans Serif

Colors
33a6d7
ec1f27

Requirements
Must have
• -Must scale to mobile
• -HTML coded files need to be provided (HTML Bootstrap)
Nice to have
• -Prefer incorporation of our logo into header bar
• -Design of 2-3 advertising banners which can be displayed on the home page
• -Prominent call to action button towards top of page 'Get a quote' or similar
• -Grid based design HTML Bootstrap

```html
<!DOCTYPE html>
<html lang="en">
<head>
<meta charset="utf-8">
<title>Arclume Lighting – Commercial Lighting Solutions</title>
<link href="https://fonts.googleapis.com/css2?family=Open+Sans:wght@400;600;700;800&display=swap" rel="stylesheet">
<style>
:root{
  --red:#ec1f27;
  --red-dark:#a8141a;
  --blue:#33a6d7;
  --blue-dark:#1f7fa8;
  --ink:#2b2b2b;
  --muted:#8a8a8a;
  --line:#e3e3e3;
  --header:#1e1f22;
  --footer:#26272a;
  --paper:#ffffff;
  --photo-dark:#1f2a24;
  --photo-field:#2a3a26;
}
*{box-sizing:border-box;margin:0;padding:0}
html,body{width:874px;height:1200px;overflow:hidden;background:var(--paper)}
body{position:relative;font-family:"Open Sans",Arial,sans-serif;color:var(--ink)}
.abs{position:absolute}

/* header */
.site-header{left:0;top:0;width:874px;height:98px;background:linear-gradient(#2c2d31,var(--header))}
.brand{left:116px;top:10px;height:50px;display:flex;align-items:center;gap:10px;color:#fff;font-weight:700;font-size:19px;letter-spacing:.5px}
.brand-mark{width:26px;height:26px;background:var(--red)}
.cta-contact{left:648px;top:14px;width:164px;height:30px;background:var(--red);color:#fff;font-size:10px;font-weight:700;letter-spacing:.5px;display:flex;align-items:center;justify-content:center}
.main-nav{right:44px;top:72px;display:flex;gap:26px;font-size:11px;color:#b9b9b9}
.main-nav .active{color:#fff;font-weight:700}

/* hero */
.hero-slide{left:116px;top:110px;width:482px;height:298px;background:linear-gradient(180deg,var(--photo-dark),var(--photo-field))}
.slide-arrow{top:244px;width:30px;height:30px;border-radius:50%;background:rgba(255,255,255,.75);display:flex;align-items:center;justify-content:center}
.promo{left:612px;width:226px;padding:16px 18px;color:#fff;text-align:center}
.promo h2{font-size:19px;font-weight:700;margin-bottom:8px}
.promo p{font-size:9px;line-height:1.5;margin-bottom:10px}
.promo .btn{display:inline-block;font-size:8px;font-weight:700;padding:6px 14px;letter-spacing:.4px}
.promo-quote{top:110px;height:138px;background:var(--red)}
.promo-quote .btn{background:var(--red-dark)}
.promo-save{top:268px;height:140px;background:var(--blue)}
.promo-save .btn{background:var(--blue-dark)}

/* solutions */
.solutions-head{left:116px;top:426px;width:722px;text-align:center}
.solutions-head .kicker{font-size:13px;color:var(--ink)}
.solutions-head h2{font-size:21px;font-weight:800;letter-spacing:.5px;line-height:1.1}
.solutions-intro{left:150px;top:472px;width:654px;font-size:9px;line-height:1.55;text-align:center;color:var(--muted)}
.solution-grid{left:116px;top:524px;width:722px;display:flex;justify-content:space-between}
.solution{width:133px;text-align:center}
.solution .thumb{width:133px;height:82px;margin-bottom:10px}
.solution h3{font-size:9px;font-weight:700;line-height:1.35;text-transform:uppercase}
.t-car{background:#7d848b}
.t-edu{background:#b3ab9c}
.t-hos{background:#9a7552}
.t-off{background:#c3d0da}
.t-war{background:#c6c9cc}

/* about */
.about-photo{left:116px;top:684px;width:248px;height:160px;background:var(--photo-field)}
.about{left:388px;top:690px;width:450px}
.about h2{font-size:20px;font-weight:800;letter-spacing:.5px;margin-bottom:6px}
.about h3{font-size:10.5px;font-weight:700;margin-bottom:6px}
.about p{font-size:9px;line-height:1.6;color:var(--muted)}
.read-more{right:36px;top:834px;display:flex;align-items:center;gap:7px;font-size:9px;color:var(--ink)}
.dot-arrow{width:18px;height:18px;border-radius:50%;background:var(--red);display:flex;align-items:center;justify-content:center}

/* blog */
.blog-title{left:116px;top:886px;font-size:18px;font-weight:800;letter-spacing:.5px}
.blog-nav{right:36px;top:890px;display:flex;gap:5px}
.blog-nav span{width:16px;height:16px;border-radius:50%;display:flex;align-items:center;justify-content:center}
.blog-list{left:116px;top:930px;width:722px;display:flex;justify-content:space-between}
.post{width:232px;display:flex;gap:10px}
.post .thumb{width:90px;height:74px;flex:none}
.post .body{width:132px}
.post h4{font-size:9px;font-weight:700;line-height:1.3;margin-bottom:4px}
.post p{font-size:8px;line-height:1.5;color:var(--muted)}
.post .date{font-size:7.5px;color:var(--blue);margin-top:3px}
.p1{background:#9aa0a6}
.p2{background:#8a6d52}
.p3{background:#b6c4cf}

/* footer */
.site-footer{left:0;top:1062px;width:874px;height:138px;background:var(--footer)}
.footer-nav{left:116px;top:1103px;display:flex;gap:8px;font-size:9px;color:#cfcfcf;align-items:center}
.footer-nav span{padding:3px 9px}
.footer-nav .active{border:1px solid #8d8d8d;border-radius:10px;color:#fff}
.social{right:44px;top:1104px;display:flex;gap:6px}
.social span{width:14px;height:14px;background:#5b5c60}
.footer-rule{left:116px;top:1132px;width:722px;height:1px;background:#3c3d41}
.contact-row{left:116px;top:1146px;width:722px;display:flex;justify-content:space-between;font-size:8px;color:#a9a9a9;align-items:center}
.contact-row .item{display:flex;align-items:center;gap:6px}
</style>
</head>
<body>

<header class="site-header abs"></header>
<div class="brand abs"><span class="brand-mark"></span>Arclume Lighting</div>
<div class="cta-contact abs">CONTACT US NOW</div>
<nav class="main-nav abs">
  <span class="active">Home</span><span>About Us</span><span>Products</span><span>Blog</span><span>Contact Us</span>
</nav>

<div class="hero-slide abs" role="img" aria-label="Photo: floodlit sports stadium at night"></div>
<div class="slide-arrow abs" style="left:124px">
  <svg width="10" height="12" viewBox="0 0 10 12"><path d="M7 1 2 6l5 5" fill="none" stroke="#333" stroke-width="2"/></svg>
</div>
<div class="slide-arrow abs" style="left:560px">
  <svg width="10" height="12" viewBox="0 0 10 12"><path d="M3 1l5 5-5 5" fill="none" stroke="#333" stroke-width="2"/></svg>
</div>

<aside class="promo promo-quote abs">
  <h2>Request for Quote</h2>
  <p>Tell us about your site and we will prepare a tailored lighting quote within two business days.</p>
  <span class="btn">REQUEST</span>
</aside>
<aside class="promo promo-save abs">
  <h2>Curabitur suscipit</h2>
  <p>Switch to LED and induction lighting and start saving on power and upkeep from day one.</p>
  <span class="btn">READ MORE</span>
</aside>

<div class="solutions-head abs">
  <div class="kicker">Our</div>
  <h2>LIGHTNING SOLUTIONS</h2>
</div>
<p class="solutions-intro abs">Efficient induction and LED fittings that cut energy and maintenance costs for every commercial space. Explore our range below to find the right lighting for your site and budget.</p>

<div class="solution-grid abs">
  <div class="solution"><div class="thumb t-car" role="img" aria-label="Photo: lit underground car park"></div><h3>Car Park Lighting</h3></div>
  <div class="solution"><div class="thumb t-edu" role="img" aria-label="Photo: bright school classroom"></div><h3>Educational<br>Lighting</h3></div>
  <div class="solution"><div class="thumb t-hos" role="img" aria-label="Photo: warmly lit hotel interior"></div><h3>Hospitality Lighting</h3></div>
  <div class="solution"><div class="thumb t-off" role="img" aria-label="Photo: open plan office with ceiling lights"></div><h3>Office Lighting</h3></div>
  <div class="solution"><div class="thumb t-war" role="img" aria-label="Photo: warehouse with high bay lighting"></div><h3>Warehouse<br>Lighting</h3></div>
</div>

<div class="about-photo abs" role="img" aria-label="Photo: stadium floodlights over a sports field"></div>
<section class="about abs">
  <h2>ABOUT US</h2>
  <h3>Welcome to the Commercial Lighting Division of Arclume Business Solutions</h3>
  <p>Arclume Lighting supplies energy efficient induction and LED lighting to car parks, schools, hotels, offices and warehouses. Our team helps facility managers and contractors choose fittings that lower running costs, reduce maintenance and improve light quality across every site.</p>
</section>
<div class="read-more abs">Read More
  <span class="dot-arrow"><svg width="7" height="9" viewBox="0 0 7 9"><path d="M1.5 1l4 3.5-4 3.5" fill="none" stroke="#fff" stroke-width="1.6"/></svg></span>
</div>

<h2 class="blog-title abs">OUR BLOG</h2>
<div class="blog-nav abs">
  <span style="background:#bdbdbd"><svg width="6" height="8" viewBox="0 0 6 8"><path d="M4.5 1 1.5 4l3 3" fill="none" stroke="#fff" stroke-width="1.5"/></svg></span>
  <span style="background:var(--red)"><svg width="6" height="8" viewBox="0 0 6 8"><path d="M1.5 1l3 3-3 3" fill="none" stroke="#fff" stroke-width="1.5"/></svg></span>
</div>
<div class="blog-list abs">
  <article class="post"><div class="thumb p1" role="img" aria-label="Photo: parking garage with new lighting"></div><div class="body"><h4>Lorem ipsum dolor sit amet</h4><p>Short update on our latest lighting projects and savings.</p><div class="date">Read more</div></div></article>
  <article class="post"><div class="thumb p2" role="img" aria-label="Photo: restaurant interior with pendant lights"></div><div class="body"><h4>Lorem ipsum dolor sit amet</h4><p>Short update on our latest lighting projects and savings.</p><div class="date">Read more</div></div></article>
  <article class="post"><div class="thumb p3" role="img" aria-label="Photo: bright retail store interior"></div><div class="body"><h4>Lorem ipsum dolor sit amet</h4><p>Short update on our latest lighting projects and savings.</p><div class="date">Read more</div></div></article>
</div>

<footer class="site-footer abs"></footer>
<nav class="footer-nav abs">
  <span class="active">Home</span><span>About Us</span><span>Products</span><span>Blog</span><span>Contact Us</span>
</nav>
<div class="social abs"><span></span><span></span><span></span><span></span></div>
<div class="footer-rule abs"></div>
<div class="contact-row abs">
  <div class="item">
    <svg width="10" height="12" viewBox="0 0 10 12"><path d="M5 11.5S1 7 1 4.5a4 4 0 0 1 8 0C9 7 5 11.5 5 11.5z" fill="#a9a9a9"/><circle cx="5" cy="4.5" r="1.4" fill="#26272a"/></svg>
    12 Kestrel Way, Brisbane QLD 4000
  </div>
  <div class="item">
    <svg width="11" height="11" viewBox="0 0 11 11"><path d="M2 1h2l1 2.5-1.3 1a6 6 0 0 0 2.8 2.8l1-1.3L10 7v2a1 1 0 0 1-1 1C5 10 1 6 1 2a1 1 0 0 1 1-1z" fill="#a9a9a9"/></svg>
    (07) 3000 1234
  </div>
  <div class="item">
    <svg width="12" height="9" viewBox="0 0 12 9"><rect x=".5" y=".5" width="11" height="8" fill="none" stroke="#a9a9a9"/><path d="M.5.5 6 5l5.5-4.5" fill="none" stroke="#a9a9a9"/></svg>
    info@arclume.com.au
  </div>
  <div class="item">© Copyright 2014 Arclume. All rights reserved.</div>
</div>

</body>
</html>
```